Business Card Design

We need a business card designed for our new company. Prefer a black card with white logo & writing.

Contact Information for Business Card

Ted Galloway, address: 7-4812 Fernhollow Road, Abbotsford, BC, V3K 8R2, Office Phone: 604-712-3390, Cell: 604-947-2164, Email: ted@resinworkshub.ca

Colors

Designer to choose only greyscale colors for use in the design.

```html
<!DOCTYPE html>
<html lang="en">
<head>
<meta charset="utf-8">
<title>Resin Works Hub – Business Card</title>
<link rel="stylesheet" href="https://fonts.googleapis.com/css2?family=Montserrat:wght@300;400;600;800&display=swap">
<style>
  :root {
    --stage: #d9d6d1;
    --card: #2a2a2a;
    --ink: #ffffff;
    --ink-soft: #e4e4e4;
    --emboss: #161616;
    --shadow: rgba(0, 0, 0, 0.35);
  }
  * { box-sizing: border-box; margin: 0; padding: 0; }
  html, body {
    width: 900px; height: 1200px; overflow: hidden;
    background: var(--stage);
    font-family: "Montserrat", sans-serif;
  }
  .canvas { position: relative; width: 900px; height: 1200px; }
  .card {
    position: absolute; left: 79px; width: 743px; height: 442px;
    background: var(--card); border-radius: 22px;
    box-shadow: 0 10px 24px var(--shadow);
    overflow: hidden; color: var(--ink);
  }
  .card--front { top: 131px; }
  .card--back { top: 638px; }

  .brand-name {
    position: absolute; left: 26px; top: 58px; width: 230px;
    font-weight: 800; font-size: 34px; line-height: 1.05;
    letter-spacing: 0.5px; color: var(--ink);
    display: flex; align-items: center; gap: 12px;
  }
  .brand-mark { width: 16px; height: 16px; background: var(--ink); flex: none; }

  .holder { position: absolute; right: 46px; top: 38px; text-align: right; }
  .holder__name { font-weight: 600; font-size: 24px; line-height: 1.2; }
  .holder__role { font-weight: 300; font-size: 15px; margin-top: 4px; color: var(--ink-soft); }

  .address {
    position: absolute; left: 40px; top: 234px;
    font-size: 15px; line-height: 20px; font-weight: 400; color: var(--ink-soft);
  }
  .contacts { position: absolute; left: 37px; top: 297px; list-style: none; }
  .contacts li {
    display: flex; align-items: center; gap: 11px;
    font-size: 15px; height: 27px; color: var(--ink-soft);
  }
  .contacts svg { width: 16px; height: 16px; fill: var(--ink); flex: none; }

  .peak-art {
    position: absolute; left: 275px; top: 272px; width: 468px; height: 150px;
    background: linear-gradient(160deg, rgba(255,255,255,0) 20%, rgba(255,255,255,0.55) 100%);
  }

  .back-brand {
    position: absolute; inset: 0;
    display: flex; align-items: center; justify-content: center;
    font-weight: 800; font-size: 58px; letter-spacing: 1px;
    color: var(--emboss);
  }
</style>
</head>
<body>
<main class="canvas">
  <section class="card card--front" aria-label="Card front">
    <div class="brand-name"><span class="brand-mark"></span><span>RESIN WORKS HUB</span></div>

    <div class="holder">
      <p class="holder__name">Ted Galloway</p>
      <p class="holder__role">owner</p>
    </div>

    <p class="address">7-4812 Fernhollow Road,<br>Abbotsford, BC, V3K 8R2</p>

    <ul class="contacts">
      <li>
        <svg viewBox="0 0 24 24" aria-hidden="true"><path d="M6.6 10.8a15.1 15.1 0 0 0 6.6 6.6l2.2-2.2c.3-.3.7-.4 1-.2 1.1.4 2.3.6 3.6.6.6 0 1 .4 1 1V20c0 .6-.4 1-1 1A17 17 0 0 1 3 4c0-.6.4-1 1-1h3.5c.6 0 1 .4 1 1 0 1.3.2 2.5.6 3.6.1.3 0 .7-.2 1z"/></svg>
        604-712-3390
      </li>
      <li>
        <svg viewBox="0 0 24 24" aria-hidden="true"><path d="M7 1h10a2 2 0 0 1 2 2v18a2 2 0 0 1-2 2H7a2 2 0 0 1-2-2V3a2 2 0 0 1 2-2zm0 3v14h10V4zm5 15.2a1.1 1.1 0 1 0 0 2.2 1.1 1.1 0 0 0 0-2.2z"/></svg>
        604-947-2164
      </li>
      <li>
        <svg viewBox="0 0 24 24" aria-hidden="true"><path d="M2 6l10 6 10-6v12H2zm0-2h20l-10 6z"/></svg>
        ted@resinworkshub.ca
      </li>
      <li>
        <svg viewBox="0 0 24 24" aria-hidden="true"><path d="M12 2a10 10 0 1 0 0 20 10 10 0 0 0 0-20zm-1 17.9A8 8 0 0 1 4.2 10L9 14.8v1a2 2 0 0 0 2 2zm6.9-2.6A2 2 0 0 0 16 16h-1v-3a1 1 0 0 0-1-1H8v-2h2a1 1 0 0 0 1-1V7h2a2 2 0 0 0 2-2v-.4a8 8 0 0 1 2.9 12.7z"/></svg>
        www.resinworkshub.ca
      </li>
    </ul>

    <div class="peak-art" role="img" aria-label="White mountain peak silhouette rising from the lower right corner"></div>
  </section>

  <section class="card card--back" aria-label="Card back">
    <div class="back-brand">RESIN WORKS HUB</div>
  </section>
</main>
</body>
</html>
```